Financial Advisor Resource Firm needs business card design

Need business card design for company in Omaha NE called Meridale Circle. We provide resources to financial advisors....workshop programs, retirement analysis, and insurance planning. I would like to see designs that use grays, greens, black, and white colors. The final design should communicate 'collaboration' and be simple yet attractive to financial planning clients. I will attached our logo and another picture of a puzzle piece coming together. I would like the incorporate the puzzle picture somehow, maybe on the back somehow, with color or just the gray scale....OR, the picture be the front of the card with 'Meridale' definition on it (see upload) and then company logo, employee name, title, address on the back (see ppt uploaded). The following disclosure needs to be included somewhere- Advisory services offered through Stonebrook Assets, LLC.
Updates

I uploaded a svg and ai file of the logo

Target Market(s)

Financial planning clients and financial advisors....so pretty diverse age range of about 40-70.

Industry/Entity Type

Financial Planning

Contact Information for Business Card

Tobias L. Fenwright, MBA
Founder/President
5287 E. Larkin Road
Suite 230
Omaha, NE 68190
Phone- (402) 555-0147
Cell- (402) 555-0183
Fax- (402) 555-0129
email- tobias@meridaleplan.example
web address- www.meridaleplan.example

Colors
1b1b1b
474747
d3d3d3
ffffff
9bcb3c
abd036

Requirements
Must have
• Must include logo provided, must be 2 sided, and must have disclosure...all of these items listed in project description

```html
<!DOCTYPE html>
<html lang="en">
<head>
<meta charset="utf-8">
<title>Meridale Circle – Business Card</title>
<link rel="stylesheet" href="https://fonts.googleapis.com/css2?family=Montserrat:wght@400;500;600&display=swap">
<style>
  :root {
    --ink: #1b1b1b;
    --ink-soft: #2a2a2a;
    --gray: #474747;
    --gray-light: #8a8a8a;
    --page: #f2f2f2;
    --white: #ffffff;
    --green: #8fc14a;
    --green-bright: #5cc23a;
    --teal: #2d7e86;
    --line: #a9d06a;
  }
  * { margin: 0; padding: 0; box-sizing: border-box; }
  html, body { width: 1200px; height: 900px; overflow: hidden; }
  body {
    background: var(--page);
    font-family: "Montserrat", Arial, sans-serif;
    color: var(--ink);
    position: relative;
  }
  .card {
    position: absolute;
    left: 296px;
    width: 609px;
    height: 348px;
    overflow: hidden;
    box-shadow: 0 14px 28px rgba(0,0,0,0.22);
  }
  /* Front */
  .card--front { top: 89px; }
  .front__photo {
    position: absolute; inset: 0 0 59px 0;
    background:
      radial-gradient(ellipse at 20% 60%, rgba(120,220,80,0.55), transparent 60%),
      linear-gradient(100deg, var(--green-bright) 0%, #3aa54a 35%, var(--teal) 70%, #3f7f95 100%);
  }
  .front__divider {
    position: absolute; left: 0; right: 0; top: 289px; height: 4px; background: var(--white);
  }
  .front__band {
    position: absolute; left: 0; right: 0; bottom: 0; height: 55px;
    background: var(--green);
    display: flex; align-items: center; justify-content: center;
    color: var(--white); font-size: 15px; letter-spacing: 0.2px;
  }
  .front__brand {
    position: absolute; left: 0; right: 0; top: 108px;
    text-align: center;
    font-size: 26px; font-weight: 600; letter-spacing: 1px;
    color: var(--ink-soft);
  }
  .front__tagline {
    position: absolute; left: 0; right: 0; top: 165px;
    text-align: center; color: var(--white);
    font-size: 15px; line-height: 19px;
  }
  .front__tagline strong { color: var(--ink-soft); font-weight: 500; }

  /* Back */
  .card--back { top: 482px; background: var(--white); }
  .back__brand {
    position: absolute; left: 37px; top: 47px;
    font-size: 22px; font-weight: 600; letter-spacing: 1px; color: var(--ink-soft);
  }
  .back__person {
    position: absolute; right: 37px; top: 118px; text-align: right;
  }
  .back__name { font-size: 22px; line-height: 26px; color: var(--green); font-weight: 400; }
  .back__name small { font-size: 15px; color: var(--ink); }
  .back__title { font-size: 15px; line-height: 19px; }
  .back__rule {
    position: absolute; left: 37px; right: 39px; top: 180px; height: 2px; background: var(--line);
  }
  .back__contacts {
    position: absolute; left: 37px; top: 201px; list-style: none;
  }
  .back__contacts li {
    display: flex; align-items: center; height: 26px; font-size: 15px;
  }
  .back__contacts svg { width: 18px; height: 18px; margin-right: 11px; fill: var(--green); }
  .back__contacts .accent { color: var(--green); }
  .back__address {
    position: absolute; right: 37px; top: 201px; text-align: right;
    font-size: 15px; line-height: 19px;
  }
  .back__disclosure {
    position: absolute; right: 37px; top: 303px;
    font-size: 9px; line-height: 11px; color: var(--gray-light);
  }
  .back__band {
    position: absolute; left: 0; right: 0; bottom: 0; height: 12px; background: var(--green);
  }
</style>
</head>
<body>

<section class="card card--front">
  <div class="front__photo" role="img" aria-label="Photograph of hands joining puzzle pieces, tinted green to blue"></div>
  <div class="front__brand">Meridale Circle</div>
  <p class="front__tagline">To come <strong>TOGETHER</strong> and <strong>UNITE</strong><br>in common interest and <strong>FOCUS</strong></p>
  <div class="front__divider"></div>
  <div class="front__band">www.meridaleplan.example</div>
</section>

<section class="card card--back">
  <div class="back__brand">Meridale Circle</div>
  <div class="back__person">
    <p class="back__name">Tobias L. Fenwright, <small>MBA</small></p>
    <p class="back__title">Founder | President</p>
  </div>
  <div class="back__rule"></div>
  <ul class="back__contacts">
    <li><svg viewBox="0 0 24 24" aria-hidden="true"><path d="M6.6 10.8a15 15 0 006.6 6.6l2.2-2.2a1 1 0 011-.25 11.4 11.4 0 003.6.6 1 1 0 011 1V20a1 1 0 01-1 1A17 17 0 013 4a1 1 0 011-1h3.5a1 1 0 011 1c0 1.25.2 2.45.6 3.6a1 1 0 01-.25 1z"/></svg>(402) 555 - 0147</li>
    <li><svg viewBox="0 0 24 24" aria-hidden="true"><path d="M7 1h10a2 2 0 012 2v18a2 2 0 01-2 2H7a2 2 0 01-2-2V3a2 2 0 012-2zm0 3v14h10V4zm5 15.5a1 1 0 100 2 1 1 0 000-2z"/></svg>(402) 555 - 0183</li>
    <li><svg viewBox="0 0 24 24" aria-hidden="true"><path d="M2 6h4v15H2zM8 3h9l3 3v15H8zm2 7v2h2v-2zm4 0v2h2v-2zm-4 4v2h2v-2zm4 0v2h2v-2zM10 5v3h8V7l-2-2z"/></svg>(402) 555 - 0129</li>
    <li><svg viewBox="0 0 24 24" aria-hidden="true"><path d="M2 5h20v2l-10 6L2 7zm0 4l10 6 10-6v10H2z"/></svg>tobias@<span class="accent">meridaleplan</span>.example</li>
  </ul>
  <p class="back__address">5287 E. Larkin Road<br>Suite 230, Omaha, NE 68190</p>
  <p class="back__disclosure">Advisory services offered through Stonebrook Assets, LLC</p>
  <div class="back__band"></div>
</section>

</body>
</html>
```